KRWB new business card design

We need a business card design for our established business which is Australia wide however based in Melbourne. We are a young team of Financial Planners who specialize in Insurance and Basic super advice for people like us.

We are people who help our clients get things done in a timely and cost effective manner whilst having a good time and a laugh along the way.

We would like this to have a consistent feel with our new e-brochure which i have attached from a color and font perspective.

Industry/Entity Type

Business

Requirements
Must have
• We do not need specific address details rather just the states we are in:

VIC/NSW/QLD/TAS
Nice to have
• Curved edge to mate the brochure

```html
<!DOCTYPE html>
<html lang="en">
<head>
<meta charset="utf-8">
<title>KRWB business card</title>
<link rel="stylesheet" href="https://fonts.googleapis.com/css2?family=Arimo:ital,wght@0,400;0,700;1,700&family=PT+Sans&display=swap">
<style>
  :root {
    --green-dark: #00a651;
    --green-light: #6cc04a;
    --ink: #1a1a1a;
    --grey-text: #6d6e70;
    --grey-head: #58595b;
    --card-white: #ffffff;
    --card-black: #161616;
    --page: #e9e6e1;
    --faint: #eef3ec;
  }
  * { margin: 0; padding: 0; box-sizing: border-box; }
  html, body { width: 1200px; height: 788px; overflow: hidden; }
  body {
    position: relative;
    background: var(--page);
    font-family: "Arimo", Arial, sans-serif;
    color: var(--ink);
  }
  .view-label {
    position: absolute;
    font-family: "PT Sans", sans-serif;
    font-size: 22px;
    color: #222;
    transform: translateX(-50%);
  }
  .card {
    position: absolute;
    width: 527px;
    height: 300px;
    overflow: hidden;
    border-radius: 30px 4px 30px 4px;
    background: var(--card-white);
    box-shadow: 0 4px 10px rgba(0,0,0,.25);
  }
  .card--front   { left: 53px;  top: 72px; }
  .card--back-1  { left: 622px; top: 74px; }
  .card--back-2  { left: 53px;  top: 445px; }
  .card--back-3  { left: 622px; top: 445px; background: radial-gradient(circle at 35% 45%, #2c2c2c, var(--card-black) 70%); }

  .swoosh { position: absolute; inset: 0; }

  .brand { position: absolute; white-space: nowrap; }
  .brand__square { display: block; background: var(--green-light); }
  .brand__name {
    display: block;
    font-weight: 700;
    line-height: 1.05;
    color: var(--ink);
  }
  .card--front .brand { left: 50px; top: 36px; }
  .card--front .brand__square { width: 110px; height: 130px; margin: 0 0 24px 30px; }
  .card--front .brand__name { font-size: 24px; }

  .card--back-1 .brand { left: 74px; top: 52px; }
  .card--back-1 .brand__square { width: 100px; height: 130px; margin: 0 0 22px 24px; }
  .card--back-1 .brand__name { font-size: 21px; }

  .card--back-3 .brand { left: 62px; top: 16px; }
  .card--back-3 .brand__square { width: 150px; height: 190px; margin: 0 0 24px 38px; }
  .card--back-3 .brand__name { font-size: 30px; color: #fff; }

  .contact { position: absolute; left: 241px; top: 45px; }
  .contact__name { font-size: 18px; font-weight: 700; color: var(--green-light); }
  .contact__role { font-size: 13px; font-weight: 700; color: var(--green-light); line-height: 1.3; }
  .contact__lines { margin-top: 20px; font-size: 14px; color: #333; line-height: 22px; list-style: none; }
  .contact__lines b { font-style: italic; font-weight: 700; }
  .contact__lines .gap { margin-top: 4px; }

  .specialties { position: absolute; }
  .specialties__title { font-size: 18px; font-weight: 700; font-style: italic; margin-bottom: 12px; }
  .specialties__list { list-style: none; font-size: 14px; font-weight: 700; line-height: 34px; }
  .specialties__list li::before { content: "\25AA\00a0"; }

  .card--back-1 .divider { position: absolute; left: 260px; top: 12px; width: 2px; height: 240px; background: linear-gradient(transparent, #777, transparent); }
  .card--back-1 .specialties { left: 320px; top: 46px; }
  .card--back-1 .specialties__title { color: var(--grey-text); }
  .card--back-1 .specialties__list { color: var(--grey-text); }
  .band {
    position: absolute; left: 0; right: 0; bottom: 0; height: 39px;
    background: var(--green-light); color: #fff;
    font-size: 14px; font-weight: 700; text-align: center; line-height: 39px;
  }

  .card--back-2 .faint-mark { position: absolute; left: 152px; top: 14px; width: 224px; height: 270px; background: var(--faint); }
  .card--back-2 .specialties { left: 0; right: 0; top: 46px; text-align: center; }
  .card--back-2 .specialties__title { color: var(--grey-head); }
  .card--back-2 .specialties__list { color: #333; }
  .tagline { position: absolute; font-size: 14px; font-weight: 700; }
  .card--back-2 .tagline { left: 0; right: 0; bottom: 16px; text-align: center; color: #444; }

  .card--back-3 .specialties { left: 314px; top: 24px; }
  .card--back-3 .specialties__title { color: #fff; }
  .card--back-3 .specialties__list { color: #fff; }
  .card--back-3 .tagline { left: 313px; top: 254px; color: var(--green-light); line-height: 18px; }
</style>
</head>
<body>
  <span class="view-label" style="left:320px;top:32px">Front</span>
  <span class="view-label" style="left:896px;top:32px">Back - 1</span>
  <span class="view-label" style="left:320px;top:403px">Back - 2</span>
  <span class="view-label" style="left:896px;top:403px">Back - 3</span>

  <section class="card card--front">
    <svg class="swoosh" viewBox="0 0 527 300" aria-hidden="true">
      <path d="M400 0 H527 V300 H432 C500 240 520 120 400 0 Z" fill="var(--green-dark)"/>
      <path d="M470 0 C520 60 540 190 468 300 H432 C520 200 510 90 440 0 Z" fill="#fff"/>
      <path d="M480 0 H527 V300 H490 C540 190 530 80 480 0 Z" fill="var(--green-dark)"/>
    </svg>
    <div class="brand">
      <span class="brand__square"></span>
      <span class="brand__name">Kestrel Ridge<br>Wealth</span>
    </div>
    <div class="contact">
      <p class="contact__name">Daniel Hartwell</p>
      <p class="contact__role">DipFP, BCom, ACR<br>Financial Adviser</p>
      <ul class="contact__lines">
        <li><b>cell</b> 0400 555 182</li>
        <li><b>phone</b> 1300 555 014</li>
        <li><b>fax</b> 03 9555 0147</li>
        <li class="gap"><b>email</b> daniel@krwb.com.au</li>
        <li class="gap"><b>web</b> www.krwb.com.au</li>
        <li>VIC/NSW/QLD/TAS</li>
      </ul>
    </div>
  </section>

  <section class="card card--back-1">
    <div class="brand">
      <span class="brand__square"></span>
      <span class="brand__name">Kestrel Ridge<br>Wealth</span>
    </div>
    <span class="divider"></span>
    <div class="specialties">
      <p class="specialties__title">Specialising in</p>
      <ul class="specialties__list">
        <li>Risk Insurance</li><li>Debt Management</li><li>Superannuation</li><li>Wealth Creation</li><li>Retirement Planning</li>
      </ul>
    </div>
    <p class="band">CLEAR GOALS, CONFIDENT LIFESTYLE</p>
  </section>

  <section class="card card--back-2">
    <span class="faint-mark"></span>
    <div class="specialties">
      <p class="specialties__title">Specialising in</p>
      <ul class="specialties__list">
        <li>Risk Insurance</li><li>Debt Management</li><li>Superannuation</li><li>Wealth Creation</li><li>Retirement Planning</li>
      </ul>
    </div>
    <p class="tagline">CLEAR GOALS, CONFIDENT LIFESTYLE</p>
  </section>

  <section class="card card--back-3">
    <div class="brand">
      <span class="brand__square"></span>
      <span class="brand__name">Kestrel Ridge<br>Wealth</span>
    </div>
    <div class="specialties">
      <p class="specialties__title">Specialising in</p>
      <ul class="specialties__list">
        <li>Risk Insurance</li><li>Debt Management</li><li>Superannuation</li><li>Wealth Creation</li><li>Retirement Planning</li>
      </ul>
    </div>
    <p class="tagline">CLEAR GOALS<br>CONFIDENT LIFESTYLE</p>
  </section>
</body>
</html>
```